The Lanterns of Quiet Harbour - 12-Week Orchard Ledger

I am finishing a book that is designed to be super hands on. It steps he reader through a 90 day roadmap - as a pick up, put down action diary style piece. The foundational idea is to speak about the Lanterns of Quiet Harbour. With a cost of living crisis this is designed to create action and understanding. I am looking for a cover for the ebook that will blow away the competitors in the category. I want it to be bright, attractive and leap off the velluma page - appeal to a wide audience. I have pasted in a file with the best selling books in the category so you can see what's working.

```html
<!DOCTYPE html>
<html lang="en">
<head>
<meta charset="utf-8">
<title>The Lanterns of Quiet Harbour – 12-Week Orchard Ledger</title>
<link href="https://fonts.googleapis.com/css2?family=Bebas+Neue&family=Montserrat:wght@600&family=Poppins:wght@600&family=Sacramento&display=swap" rel="stylesheet">
<style>
  :root {
    --stage: #3d3648;
    --paper: #fdf6f0;
    --sand: #dac6b3;
    --sage: #55875c;
    --amber: #d58535;
    --amber-pale: #f1d6ba;
    --ink: #2a2528;
    --white: #ffffff;
  }
  html, body {
    margin: 0;
    padding: 0;
    width: 1200px;
    height: 2400px;
    overflow: hidden;
    background: var(--stage);
  }
  .cover {
    position: absolute;
    left: 80px;
    top: 371px;
    width: 1040px;
    height: 1658px;
    background: var(--paper);
    box-shadow: 0 30px 60px rgba(0, 0, 0, 0.35);
    overflow: hidden;
  }
  .cover__texture {
    position: absolute;
    inset: 0;
    background:
      radial-gradient(ellipse 90% 55% at 45% 95%, rgba(200, 190, 180, 0.28), transparent 70%),
      linear-gradient(180deg, rgba(230, 222, 214, 0) 30%, rgba(225, 216, 207, 0.35) 100%);
  }
  .title {
    position: absolute;
    left: 75px;
    margin: 0;
    font-family: "Bebas Neue", "Arial Narrow", sans-serif;
    font-weight: 400;
    line-height: 1;
    white-space: nowrap;
  }
  .title--the { top: 78px; font-size: 250px; color: var(--sand); }
  .title--lanterns { top: 276px; font-size: 250px; color: var(--sand); }
  .title--quiet { top: 580px; font-size: 290px; color: var(--sage); }
  .title--harbour { top: 803px; font-size: 290px; color: var(--amber); }
  .title-joiner {
    position: absolute;
    left: 80px;
    top: 470px;
    margin: 0;
    font-family: "Sacramento", cursive;
    font-size: 150px;
    line-height: 1;
    color: var(--sand);
  }
  .subtitle-band {
    position: absolute;
    left: 72px;
    right: 0;
    top: 1107px;
    height: 193px;
    border-radius: 14px 0 0 14px;
    background: linear-gradient(90deg, var(--amber) 0%, #e3a468 45%, var(--amber-pale) 100%);
  }
  .subtitle {
    position: absolute;
    left: 36px;
    top: 14px;
    margin: 0;
    font-family: "Poppins", sans-serif;
    font-weight: 600;
    font-size: 66px;
    line-height: 1.22;
    color: var(--white);
  }
  .author {
    position: absolute;
    left: 80px;
    top: 1468px;
    margin: 0;
    font-family: "Montserrat", sans-serif;
    font-weight: 600;
    font-size: 48px;
    letter-spacing: 0.14em;
    color: var(--ink);
  }
</style>
</head>
<body>
  <main class="cover">
    <div class="cover__texture" role="img" aria-label="Faint fanned banknote illustration across the cover background"></div>
    <p class="title title--the">THE</p>
    <p class="title title--lanterns">LANTERNS</p>
    <p class="title-joiner">of</p>
    <p class="title title--quiet">QUIET</p>
    <p class="title title--harbour">HARBOUR</p>
    <div class="subtitle-band">
      <p class="subtitle">12-Week<br>Orchard Ledger</p>
    </div>
    <p class="author">AUTHOR’S NAME</p>
  </main>
</body>
</html>
```